Website for a Steadwell, an HVAC company.

We are a company that provides residential and commercial service. We don’t need any widgets other than a call to action where customers can message us. Though we have very few google reviews, they are all great and would like to see those populated. Simple and modern is the style. I included our logo and a pic of our vans.

Target Market(s)

Residential customers

Coding

Coded - Design and coding required

Number of Pages Required

1 page

Font styles to use
Sans Serif

Colors
0054AA
0677BA
7BADD7
CADEEF
E8F1F8
EE7325
F08F49
F5BC92
FAE3D3
FDF4ED

```html
<!DOCTYPE html>
<html lang="en">
<head>
<meta charset="utf-8">
<title>Steadwell Heating and Air</title>
<link href="https://fonts.googleapis.com/css2?family=Poppins:wght@300;400;500;600;700&display=swap" rel="stylesheet">
<style>
:root{
  --blue-dark:#0054AA;
  --blue:#0677BA;
  --blue-mid:#7BADD7;
  --blue-light:#CADEEF;
  --blue-pale:#E8F1F8;
  --orange:#EE7325;
  --orange-mid:#F08F49;
  --orange-soft:#F5BC92;
  --orange-light:#FAE3D3;
  --orange-pale:#FDF4ED;
  --ink:#1f1f1f;
  --text:#333;
  --grey-bg:#f3f3f3;
  --line:#d9d9d9;
  --btn-grad:linear-gradient(90deg,#2a7fde,#3cc4ea);
}
*{box-sizing:border-box;margin:0;padding:0}
html,body{width:1200px;height:4816px;overflow:hidden;background:#fff}
body{font-family:"Poppins",sans-serif;color:var(--text);position:relative}
section,header,footer{position:relative;width:1200px}
.abs{position:absolute}
.btn{position:absolute;display:flex;align-items:center;justify-content:center;color:#fff;font-weight:500;border-radius:40px;background:var(--btn-grad)}
.eyebrow{font-size:17px;font-weight:500;color:var(--orange);letter-spacing:1px}
.title{font-size:46px;font-weight:500;color:var(--blue)}
.lorem{font-size:16px;line-height:1.6;color:var(--text)}
.center{left:0;right:0;text-align:center}
.eyebrow-lines{display:flex;align-items:center;justify-content:center;gap:12px}
.eyebrow-lines::before,.eyebrow-lines::after{content:"";width:40px;height:2px;background:var(--orange)}

/* header */
.site-header{height:144px}
.brand{left:40px;top:28px;display:flex;align-items:center;gap:12px}
.brand-dot{width:34px;height:34px;border-radius:50%;background:var(--orange)}
.brand-name{font-size:26px;font-weight:700;color:var(--blue-dark);letter-spacing:1px}
.main-nav{left:292px;top:58px;display:flex;gap:44px;font-size:15px;font-weight:500;color:var(--ink)}
.main-nav .active{color:var(--orange)}
.appt-btn{left:916px;top:40px;width:230px;height:52px;background:linear-gradient(90deg,#EE7325,#f5a031);font-size:15px}

/* hero */
.hero{height:576px;background:linear-gradient(90deg,#e9e6e2 0%,#f2f0ee 60%,#f6f5f4 100%)}
.hero-photo{left:0;top:0;width:620px;height:576px;background:linear-gradient(120deg,#d7d2cc,#ece8e3 60%,#f4f2f0)}
.hero-text{left:608px;top:106px}
.hero-h{font-size:47px;font-weight:700;line-height:1.2;white-space:nowrap}
.hero-h .o{color:var(--orange)} .hero-h .b{color:#2b9fe0} .hero-h .d{color:#333}
.hero-text p{margin-top:16px;width:540px;font-size:15px}
.know-btn{left:608px;top:370px;width:196px;height:56px;font-size:16px;gap:12px}
.arrow-circ{width:36px;height:36px;border-radius:50%;background:#fff;display:flex;align-items:center;justify-content:center}

/* about */
.about{height:540px}
.about .eyebrow{left:112px;top:96px;display:flex;align-items:center;gap:10px}
.about .eyebrow::after{content:"";width:40px;height:2px;background:var(--orange)}
.about .title{left:108px;top:116px}
.about .lorem{left:108px;top:180px;width:566px;font-size:14px;line-height:1.7}
.read-btn{left:108px;top:400px;width:156px;height:54px;font-size:16px}
.tile{position:absolute;background:linear-gradient(135deg,#cfd3d7,#eef0f2);border-radius:26px}

/* services */
.services{height:840px;background:var(--grey-bg)}
.services .eyebrow{top:104px}
.services .title{top:124px}
.card{position:absolute;top:240px;height:400px;background:#f7f7f7;border-radius:6px;box-shadow:0 6px 24px rgba(0,0,0,.07);text-align:center}
.card .icon{margin:52px auto 0;width:86px;height:86px;border-radius:50%;border:2px solid var(--orange-soft);display:flex;align-items:center;justify-content:center}
.card h3{margin-top:46px;font-size:22px;font-weight:600;color:var(--ink)}
.card p{margin:12px auto 0;width:250px;font-size:14px;line-height:1.5;font-weight:500;color:#333}
.card .more{display:inline-block;margin-top:24px;font-size:15px;font-weight:500;color:#333;text-decoration:underline}
.card.featured{background:var(--orange);top:220px;height:440px;box-shadow:0 12px 40px rgba(238,115,37,.35)}
.card.featured h3,.card.featured p,.card.featured .more{color:#fff}
.card.featured .icon{border-color:#fff}
.viewall-btn{left:518px;top:732px;width:164px;height:54px;font-size:17px}

/* stats */
.stats{height:580px;display:flex;justify-content:center;padding-top:40px}
.stat{width:280px;height:260px;text-align:left;padding:72px 0 0 0;position:relative}
.stat + .stat{border-left:2px solid var(--line);padding-left:40px}
.stat .num{font-size:94px;font-weight:400;color:var(--orange);line-height:1}
.stat .lbl{margin-top:18px;font-size:19px;font-weight:500;color:var(--ink)}
.banner{position:absolute;left:0;top:2420px;width:1200px;height:572px;background:linear-gradient(90deg,#c9d3a7 0%,#ece9e2 35%,#d8d6d2 70%,#b9b8b4 100%)}
.banner .kicker{top:112px;font-size:30px;font-weight:600;color:#111}
.banner .big{top:152px;font-size:80px;font-weight:700;line-height:1.08;color:#000}
.contact-btn{left:406px;top:390px;width:388px;height:82px;font-size:30px}

/* reviews */
.reviews{position:absolute;top:2992px;height:680px;background:var(--grey-bg)}
.reviews .eyebrow{top:44px}
.reviews .title{top:64px}
.review{position:absolute;top:150px;width:440px;height:296px;border:1.5px solid #cfcfcf;border-radius:26px;background:#f6f6f6;padding:24px 34px}
.review .q{font-size:110px;line-height:.9;color:var(--orange);font-family:"Poppins",sans-serif;height:60px}
.review .head{display:flex;justify-content:space-between;align-items:center;margin-top:12px}
.review h4{font-size:15px;font-weight:500;color:var(--orange)}
.review .stars{color:#f2a623;font-size:16px;letter-spacing:2px}
.review p{margin-top:14px;font-size:14px;line-height:1.55;color:#444}
.reviewer{position:absolute;top:488px;display:flex;align-items:center;gap:16px}
.avatar{width:60px;height:60px;border-radius:50%}
.reviewer b{display:block;font-size:13px;color:var(--blue);font-weight:600}
.reviewer span{font-size:12px;color:#555}
.dots{top:596px;display:flex;justify-content:center;gap:8px}
.dots i{width:10px;height:10px;border-radius:50%;background:#d4d4d4}
.dots i:first-child{background:#888}

/* contact */
.contact{position:absolute;top:3672px;height:668px}
.contact .eyebrow{left:80px;top:80px}
.contact .title{left:80px;top:100px}
.contact .intro{left:88px;top:184px;font-size:15.5px;color:#222}
.field{position:absolute;border:1.5px solid #d0d0d0;border-radius:4px;background:#fff;font-size:13px;color:#999;padding:12px 14px}
.submit-btn{left:94px;top:568px;width:114px;height:42px;font-size:15px}

/* footer */
.site-footer{position:absolute;top:4340px;height:476px;background:#fff}
.foot-brand{left:196px;top:104px;text-align:center}
.foot-brand .brand-dot{margin:0 auto 12px;width:60px;height:60px}
.foot-brand .brand-name{font-size:26px}
.socials{left:212px;top:216px;display:flex;gap:12px}
.socials i{width:34px;height:34px;border-radius:50%;background:#2a8fe0}
.foot-title{font-size:23px;font-weight:600;color:#111}
.foot-links{left:532px;top:76px}
.foot-links ul{list-style:none;margin-top:22px}
.foot-links li{font-size:15px;color:#222;margin-bottom:12px;display:flex;align-items:center;gap:14px}
.foot-links li::before{content:"";width:7px;height:7px;border-radius:50%;background:var(--blue)}
.foot-contact{left:800px;top:76px}
.ci{display:flex;align-items:center;gap:16px;margin-top:22px;font-size:14px;color:#222;line-height:1.4}
.ci .ic{width:36px;height:36px;border-radius:50%;background:var(--blue);display:flex;align-items:center;justify-content:center;flex:none}
.foot-rule{left:120px;right:120px;top:380px;height:2px;background:var(--blue-light)}
.copyright{top:416px;font-size:15px;color:#111}
</style>
</head>
<body>

<header class="site-header">
  <div class="abs brand"><span class="brand-dot"></span><span class="brand-name">STEADWELL</span></div>
  <nav class="abs main-nav">
    <span class="active">HOME</span><span>ABOUT US</span><span>OUR SERVICES</span><span>TESTIMONIALS</span><span>CONTACT US</span>
  </nav>
  <a class="btn appt-btn">Make A Appointment</a>
</header>

<section class="hero">
  <div class="abs hero-photo" role="img" aria-label="Woman relaxing on a sofa in a cool, comfortable living room"></div>
  <div class="abs hero-text">
    <h1 class="hero-h"><span class="o">HEATING AND</span><br><span class="b">AIR CONDITIONING</span><br><span class="d">COMFORT SPECIALIST</span></h1>
    <p class="lorem">Lorem ipsum dolor sit amet, consectetur adipiscing elit, sed do eiusmod tempor incididunt ut labore et dolore magna aliqua.</p>
  </div>
  <a class="btn know-btn">Know More <span class="arrow-circ"><svg width="18" height="18" viewBox="0 0 18 18"><path d="M3 9h11M10 5l4 4-4 4" stroke="#2a7fde" stroke-width="2" fill="none" stroke-linecap="round"/></svg></span></a>
</section>

<section class="about">
  <div class="abs eyebrow">WHO WE ARE</div>
  <h2 class="abs title">ABOUT US</h2>
  <p class="abs lorem">Lorem ipsum dolor sit amet, consectetur adipiscing elit, sed do eiusmod tempor incididunt ut labore et dolore magna aliqua. Ut enim ad minim veniam, quis nostrud exercitation ullamco laboris nisi ut aliquip ex ea commodo consequat. Duis aute irure dolor in reprehenderit in voluptate velit esse cillum dolore eu fugiat nulla pariatur. Excepteur sint occaecat cupidatat non proident, sunt in culpa qui officia deserunt mollit anim id est laborum.</p>
  <a class="btn read-btn">Read More</a>
  <div class="tile" style="left:680px;top:72px;width:188px;height:188px" role="img" aria-label="Hand adjusting a wall thermostat"></div>
  <div class="tile" style="left:884px;top:72px;width:188px;height:188px;background:linear-gradient(135deg,#e5e8eb,#f6f7f8)" role="img" aria-label="Wall mounted air conditioner"></div>
  <div class="tile" style="left:680px;top:276px;width:188px;height:188px;background:linear-gradient(135deg,#2c2f33,#8a8e93)" role="img" aria-label="Thermostat control close up"></div>
  <div class="tile" style="left:884px;top:276px;width:188px;height:188px;background:linear-gradient(135deg,#d9dde1,#f0f2f4)" role="img" aria-label="Bright interior with air conditioning unit"></div>
</section>

<section class="services">
  <div class="abs center eyebrow eyebrow-lines">WHAT WE DO</div>
  <h2 class="abs center title">OUR SERVICES</h2>
  <div class="card" style="left:96px;width:328px">
    <div class="icon"><svg width="46" height="46" viewBox="0 0 46 46" fill="none" stroke="#EE7325" stroke-width="2"><rect x="5" y="10" width="36" height="16" rx="2"/><path d="M10 21h26M14 32v6M23 32v8M32 32v6"/></svg></div>
    <h3>AC INSTALLATION</h3>
    <p>Lorem ipsum dolor sit amet, consectetur adipiscing elit, sed do eiusmod tempor incididunt ut labore et dolore</p>
    <span class="more">READ MORE</span>
  </div>
  <div class="card featured" style="left:440px;width:320px">
    <div class="icon"><svg width="46" height="46" viewBox="0 0 46 46" fill="none" stroke="#fff" stroke-width="2"><rect x="5" y="10" width="36" height="16" rx="2"/><path d="M10 21h26M17 34l12 6M29 30l-6 10"/></svg></div>
    <h3>AC REPAIR</h3>
    <p>Lorem ipsum dolor sit amet, consectetur adipiscing elit, sed do eiusmod tempor incididunt ut labore et dolore</p>
    <span class="more">READ MORE</span>
  </div>
  <div class="card" style="left:784px;width:320px">
    <div class="icon"><svg width="46" height="46" viewBox="0 0 46 46" fill="none" stroke="#EE7325" stroke-width="2"><rect x="5" y="10" width="36" height="16" rx="2"/><path d="M10 21h26M16 32l14 8M30 32l-14 8"/></svg></div>
    <h3>AC MAINTENANCE</h3>
    <p>Lorem ipsum dolor sit amet, consectetur adipiscing elit, sed do eiusmod tempor incididunt ut labore et dolore</p>
    <span class="more">READ MORE</span>
  </div>
  <a class="btn viewall-btn">View All</a>
</section>

<section class="stats">
  <div class="stat"><div class="num">10+</div><div class="lbl">Year of Experience</div></div>
  <div class="stat"><div class="num">20+</div><div class="lbl">Professional Team</div></div>
  <div class="stat"><div class="num">10K</div><div class="lbl">Happy Customers</div></div>
  <div class="stat"><div class="num">10</div><div class="lbl">Branches</div></div>
</section>

<div class="banner" role="img" aria-label="Green leaves beside a wall mounted air conditioner">
  <div class="abs center kicker">BEST AIR CONDITIONING SERVICES</div>
  <div class="abs center big">AIR CONDITIONING<br>INSTALLATION</div>
  <a class="btn contact-btn">Contact Us</a>
</div>

<section class="reviews">
  <div class="abs center eyebrow eyebrow-lines">TESTIMONIALS</div>
  <h2 class="abs center title">CLIENT REVIEWS</h2>
  <div class="review" style="left:112px">
    <div class="q">&ldquo;</div>
    <div class="head"><h4>Awesome Support...</h4><span class="stars">★★★★★</span></div>
    <p>"Lorem ipsum dolor sit amet, consectetur adipiscing elit, sed do eiusmod tempor incididunt ut labore et dolore magna aliqua. Quis ipsum suspendisse ultrices gravida. Risus commodo viverra maecenas accumsan lacus vel facilisis."</p>
  </div>
  <div class="review" style="left:660px">
    <div class="q">&ldquo;</div>
    <div class="head"><h4>Great Services...</h4><span class="stars">★★★★★</span></div>
    <p>"Lorem ipsum dolor sit amet, consectetur adipiscing elit, sed do eiusmod tempor incididunt ut labore et dolore magna aliqua. Quis ipsum suspendisse ultrices gravida. Risus commodo viverra maecenas accumsan lacus vel facilisis."</p>
  </div>
  <div class="reviewer" style="left:220px"><div class="avatar" style="background:linear-gradient(135deg,#8a8f96,#d3d6da)" role="img" aria-label="Customer portrait"></div><div><b>MARCUS HALE</b><span>Lorem Ipsum</span></div></div>
  <div class="reviewer" style="left:728px"><div class="avatar" style="background:linear-gradient(135deg,#d9a77a,#f1d9c2)" role="img" aria-label="Customer portrait"></div><div><b>DANIEL ORTIZ</b><span>Lorem Ipsum</span></div></div>
  <div class="abs center dots"><i></i><i></i><i></i><i></i></div>
</section>

<section class="contact">
  <div class="abs eyebrow">GET IN TOUCH</div>
  <h2 class="abs title">CONTACT US</h2>
  <p class="abs intro">For more information Please fill out the following and we will be in touch shortly.</p>
  <div class="field" style="left:94px;top:240px;width:270px;height:48px">First Name</div>
  <div class="field" style="left:386px;top:240px;width:270px;height:48px">Last Name</div>
  <div class="field" style="left:94px;top:308px;width:270px;height:48px">Phone</div>
  <div class="field" style="left:386px;top:308px;width:270px;height:48px">Email</div>
  <div class="field" style="left:94px;top:376px;width:562px;height:160px">Message</div>
  <a class="btn submit-btn">Submit</a>
  <div class="tile" style="left:712px;top:188px;width:192px;height:192px;background:linear-gradient(135deg,#3a3d41,#9a9ea3)" role="img" aria-label="Air conditioning unit close up"></div>
  <div class="tile" style="left:920px;top:188px;width:192px;height:192px;background:linear-gradient(135deg,#4a4d52,#b5b8bc)" role="img" aria-label="Air vent on dark wall"></div>
  <div class="tile" style="left:712px;top:396px;width:192px;height:192px;background:linear-gradient(135deg,#6f7378,#c6c9cc)" role="img" aria-label="Technician servicing an indoor unit"></div>
  <div class="tile" style="left:920px;top:396px;width:192px;height:192px;background:linear-gradient(135deg,#5c6066,#d0d3d6)" role="img" aria-label="Technician with tools at work"></div>
</section>

<footer class="site-footer">
  <div class="abs foot-brand"><div class="brand-dot"></div><div class="brand-name">STEADWELL</div></div>
  <div class="abs socials"><i></i><i></i><i></i></div>
  <div class="abs foot-links">
    <div class="foot-title">LINKS</div>
    <ul><li>Home</li><li>About Us</li><li>Services</li><li>Testimonials</li><li>Contact Us</li></ul>
  </div>
  <div class="abs foot-contact">
    <div class="foot-title">CONTACT US</div>
    <div class="ci"><span class="ic"><svg width="16" height="16" viewBox="0 0 16 16"><path d="M8 1a5 5 0 0 0-5 5c0 4 5 9 5 9s5-5 5-9a5 5 0 0 0-5-5z" fill="#fff"/><circle cx="8" cy="6" r="2" fill="#0677BA"/></svg></span><span>465, Lorem Ipsum<br>Lorem Ipsum , Lorem Ipsum</span></div>
    <div class="ci"><span class="ic"><svg width="16" height="16" viewBox="0 0 16 16"><path d="M4 1l3 3-2 2c1 2 2 3 4 4l2-2 3 3-2 2C7 13 3 9 2 3z" fill="#fff"/></svg></span><span>+1 000 888 8888</span></div>
    <div class="ci"><span class="ic"><svg width="16" height="16" viewBox="0 0 16 16"><rect x="2" y="4" width="12" height="9" rx="1" fill="#fff"/><path d="M2 5l6 4 6-4" stroke="#0677BA" fill="none"/></svg></span><span>info@companyname.com</span></div>
  </div>
  <div class="abs foot-rule"></div>
  <div class="abs center copyright">Copyright © 2025 All Rights Reserved By Company Name</div>
</footer>

</body>
</html>
```